Yoga/movement guide/teacher for adult yoga practice and kid yoga

What is the positioning or mission statement of your company? to guide individuals in a yoga-based safe and sustainable movement practice applicable to all ages and body types. Currently my focus is working with children in daycare and school settings, but my goal is to expand into private yoga practice for adults, and potentially as part of rented space in studios. I hope to find a way to work with children AND adults (so would love for logo to be appealing to both), but current focus is with children based on need and demand in the community. yoga for children also compliments my backround as a pediatrician/neonatologist, and I greatly miss interacting with children. I also want to emphasize a yoga/movement practice that is focused more on what one feels internally through movement. NOT what one looks like asthetically. I believe in removing all mirrors from yoga/movement practice. It should be an experience of movement/poses/yoga through appropriate cueing and education. It is not about the details of how far the knee should bend, or how high the leg should be. Focusing on foudation first, core, then core engagement and ultimately expression of poses/movements. A focus on strength, stability and mobility, not just flexibility, which is the common perception/association with yoga. I also want individuals to learn to be an advocate of their own health. Through guidance, I hope for individuals to connect with their body so they know themselves so well to be able to advocate for themselves in the modern healthcare world. This internal experience and connection is so essential in a world where modern medicine has become a business and it is all about making a dollar. the connection with patients is lost, and individuals need to learn to empower themselves and through their new found voice to be able to articulate what is wrong.<br/>Does your company have a tagline or slogan that should be included with the logo? "Move With Inner Light"<br/>What do you hope your company can be known for? Accessible yoga for a sustained practice. A guided movement practice where one gains information and knowledge of oneself through a mind/body connection. For one feel good physically with a new awaraness of their internal radiance that exists in all beings. Physical rejuvenation egnites a light and increases energy to flow through the physical body, which ultimately tranlates into works of kindness for others and out in the world. <br/>What color palettes might you prefer? why? love the colors currently chosen<br/>Where will the logo be primarily used? initially business cards, but hopefully future websites, t-shirts, and potentially local magazine adds. Also starting with a small couple of banners for community events in the area. I currently practice as a nomad out of my car :)<br/>Are there any elements you would prefer to see in the logo? Movement. A modern depiction of a human body/figure practicing movement. Hoping to avoid a stereotypical yoga pose per say, just because I want to people to think of it more of a movement practice with yoga roots. Modern yoga. There are elements of breathing and connecting with oneself through the flow of breath and movement, but I do not focus on the meditative/cerebral aspect of the yoga practice. What I teach is almost reaching a meditative state through movement. I personally don't practice, nor resonate with just seated meditation. just not my thing :)<br/>In your opinion, what defines a well-designed logo? curiosity. enough info for individuals to think they know what it means, but want to know more. invokes curiosity, but not too abstract. Reproducible. not too complicated. I want also to invoke a community feel, so a design that appeals to all people within a community. <br/>What is your preference in reference to icons, typography, spokespeople (characters), etc.? modern design. I love the idea of a logo for my purposes, to invoke a sense of movement from within. So not too static. <br/>What words or icons must be included in the logo? movement with yoga roots. <br/>What logos do you like and why? A representation, but not exact. I think some ambiguity is intriguing for others, and also memorable. I want it to be an artistic representation of movement/yoga<br/>What logos do you dislike and why? too busy, too loud. <br/>In your opinion, what is the primary purpose for a logo? association<br/>Who is the primary target audience? (who is most likely to use your services/product?) Children and their parents, but ultimately to expand into teaching adults. I even have aspirations of prenatal and post-natal yoga. Potentially incorporating infants. <br/>Who currently uses your product the most? n/a (working in schools/daycare currently. It is currently all volunteer)<br/>Are you pleased with the range of people your company serves? n/a<br/>Are you looking to expand, modify, or completely change your target audience? or will it remain the same? yes! expand into an adult audience. <br/>How do you plan to focus on your target audience? currently by working through schools and daycares. hopefully ultimately through after school care programs and then offering kid yoga in an existing yoga studio (working on this with Q Studio in Ridgeland, currently)<br/>What are your main forms of advertising? word of mouth, schools, daycares. Happy kids talking to their parents about the yoga class they took and happy teachers :)<br/>How do most customers find out about your company?<br/>Which gender are you targeting? All genders! However, with kid yoga, often the maternal individual in the child's life is more involved with decision making as far as extracurricular activities

Target Market(s)

individuals and families interested in wellness and feeling great

Contact Information for Business Card

Dana Whitford
Yoga Instructor
RYT-200, RCYT

certified yoga teacher for adults and children

Colors

Designer to choose colors to be used in the design.

Requirements
Must have
• "Move With Inner Light"
Nice to have
• logo with same colors

```html
<!DOCTYPE html>
<html lang="en">
<head>
<meta charset="UTF-8">
<title>Glowfield Studios — Business Cards</title>
<link href="https://fonts.googleapis.com/css2?family=Amatic+SC:wght@700&family=Open+Sans:wght@400;600;700&display=swap" rel="stylesheet">
<style>
  :root {
    --backdrop: #d5d5d5;
    --slate: #7f7f7e;
    --paper: #ffffff;
    --sun: #fde04e;
    --teal: #5ecbd1;
    --ink: #4a4a4a;
    --ink-soft: #6b6b6b;
  }
  * { margin: 0; padding: 0; box-sizing: border-box; }
  html, body { width: 1200px; height: 900px; overflow: hidden; }
  body {
    background: var(--backdrop);
    font-family: "Open Sans", Arial, sans-serif;
    position: relative;
  }
  .card {
    position: absolute;
    width: 525px;
    height: 300px;
    overflow: hidden;
    top: 300px;
  }
  .card--back { left: 50px; background: var(--slate); }
  .card--front { left: 625px; background: var(--paper); }

  /* back side */
  .sun-art {
    position: absolute;
    left: -30px;
    top: 110px;
    width: 280px;
    height: 280px;
  }
  .swirl { position: absolute; }
  .swirl--large { right: -40px; top: 130px; width: 130px; height: 130px; }
  .swirl--top { right: 110px; top: -20px; width: 70px; height: 70px; }
  .swirl--dot-a { left: 300px; top: 130px; width: 26px; height: 26px; }
  .swirl--dot-b { left: 340px; top: 178px; width: 22px; height: 22px; }
  .swirl--dot-c { left: 270px; top: 250px; width: 30px; height: 30px; }
  .tagline {
    position: absolute;
    right: 40px;
    top: 70px;
    font-family: "Amatic SC", "Comic Sans MS", cursive;
    font-weight: 700;
    font-size: 22px;
    letter-spacing: 4px;
    color: var(--teal);
    text-transform: uppercase;
    white-space: nowrap;
  }

  /* front side */
  .brand {
    position: absolute;
    left: 36px;
    top: 122px;
    display: flex;
    align-items: center;
    gap: 12px;
  }
  .brand-mark {
    width: 44px;
    height: 44px;
    border-radius: 50%;
    background: var(--sun);
    flex: none;
  }
  .brand-text { display: flex; flex-direction: column; }
  .brand-name {
    font-size: 21px;
    font-weight: 400;
    color: var(--ink);
    line-height: 1.1;
    white-space: nowrap;
  }
  .brand-tagline {
    margin-top: 4px;
    font-size: 8px;
    letter-spacing: 2px;
    text-transform: uppercase;
    color: var(--teal);
    white-space: nowrap;
  }
  .contact {
    position: absolute;
    left: 305px;
    top: 62px;
  }
  .contact-name {
    font-size: 20px;
    font-weight: 700;
    color: var(--teal);
  }
  .contact-role {
    font-size: 13px;
    color: var(--ink-soft);
    margin-top: 2px;
  }
  .divider {
    width: 36px;
    height: 3px;
    background: var(--sun);
    margin: 18px 0 16px;
  }
  .contact-list { list-style: none; }
  .contact-item {
    display: flex;
    align-items: center;
    gap: 8px;
    font-size: 12px;
    color: var(--ink);
    line-height: 1.7;
    white-space: nowrap;
  }
  .contact-icon { width: 11px; height: 11px; flex: none; }
</style>
</head>
<body>

  <section class="card card--back" aria-label="Business card back">
    <svg class="sun-art" viewBox="0 0 280 280" role="img" aria-label="Hand-drawn yellow sun illustration with a flowing teal figure">
      <circle cx="140" cy="140" r="110" fill="var(--sun)"/>
    </svg>
    <svg class="swirl swirl--large" viewBox="0 0 100 100" role="img" aria-label="Large yellow spiral ornament"><circle cx="50" cy="50" r="50" fill="var(--sun)"/></svg>
    <svg class="swirl swirl--top" viewBox="0 0 100 100" role="img" aria-label="Yellow spiral ornament"><circle cx="50" cy="50" r="50" fill="var(--sun)"/></svg>
    <svg class="swirl swirl--dot-a" viewBox="0 0 100 100" role="img" aria-label="Small yellow spiral ornament"><circle cx="50" cy="50" r="50" fill="var(--sun)"/></svg>
    <svg class="swirl swirl--dot-b" viewBox="0 0 100 100" role="img" aria-label="Small yellow spiral ornament"><circle cx="50" cy="50" r="50" fill="var(--sun)"/></svg>
    <svg class="swirl swirl--dot-c" viewBox="0 0 100 100" role="img" aria-label="Small yellow spiral ornament"><circle cx="50" cy="50" r="50" fill="var(--sun)"/></svg>
    <p class="tagline">Move With Inner Light</p>
  </section>

  <section class="card card--front" aria-label="Business card front">
    <div class="brand">
      <span class="brand-mark" aria-hidden="true"></span>
      <div class="brand-text">
        <span class="brand-name">Glowfield Studios</span>
        <span class="brand-tagline">Move With Inner Light</span>
      </div>
    </div>

    <div class="contact">
      <h1 class="contact-name">Noah Bennett</h1>
      <p class="contact-role">Founder</p>
      <div class="divider"></div>
      <ul class="contact-list">
        <li class="contact-item">
          <svg class="contact-icon" viewBox="0 0 12 12" aria-hidden="true"><path d="M3 1 L5 3.5 L4 5 Q5 7 7 8 L8.5 7 L11 9 L9.5 11 Q4 10.5 1 3 Z" fill="var(--teal)"/></svg>
          555-014-2290
        </li>
        <li class="contact-item">
          <svg class="contact-icon" viewBox="0 0 12 12" aria-hidden="true"><rect x="0.8" y="2.3" width="10.4" height="7.4" fill="none" stroke="var(--teal)" stroke-width="1.4"/><path d="M1 2.6 L6 6.6 L11 2.6" fill="none" stroke="var(--teal)" stroke-width="1.4"/></svg>
          danawhitford@brightmail.net
        </li>
        <li class="contact-item">
          <svg class="contact-icon" viewBox="0 0 12 12" aria-hidden="true"><circle cx="6" cy="6" r="5.2" fill="var(--teal)"/><path d="M1 6 H11 M6 1 Q3 6 6 11 M6 1 Q9 6 6 11" fill="none" stroke="#fff" stroke-width="0.8"/></svg>
          www.glowfieldstudios.com
        </li>
      </ul>
    </div>
  </section>

</body>
</html>
```